RWT Fittings Ltd Business Cards

We need a business card with our business logo. We provide window and door installations on high-rises in west coast British Colombia, Canada.

I would like my business information and details on one side of the card, and the other side the company name with logo

Target Market(s)

General Contractors

Industry/Entity Type

Construction

Contact Information for Business Card

one side i want my company name and logo in the dark theme logo that i provided

Requirements
Must have
• Marco Peltieri, 16045518293, RWTFittings@mailbox-demo.com, 1407-5194 Linden Row Burnaby BC, V5H 2K9, Owner & Manager

```html
<!DOCTYPE html>
<html lang="en">
<head>
<meta charset="utf-8">
<title>RWT Fittings Ltd – Business Cards</title>
<link rel="stylesheet" href="https://fonts.googleapis.com/css2?family=Open+Sans:wght@400;700&display=swap">
<style>
  :root {
    --bg-light: #5a5a5a;
    --bg-dark: #151515;
    --card: #1b1b1b;
    --blue: #29a9e1;
    --grey: #a2a2a2;
    --white: #f2f2f2;
  }
  * { box-sizing: border-box; margin: 0; padding: 0; }
  html, body { width: 1200px; height: 780px; overflow: hidden; }
  body {
    background: linear-gradient(135deg, var(--bg-light) 0%, #2c2c2c 55%, var(--bg-dark) 100%);
    font-family: "Open Sans", Arial, sans-serif;
    display: flex;
    align-items: center;
    justify-content: center;
    gap: 40px;
  }
  .card {
    position: relative;
    width: 540px;
    height: 309px;
    background: var(--card);
    overflow: hidden;
    box-shadow: 0 14px 30px rgba(0,0,0,.55);
  }

  /* Front: contact side */
  .card-front .accent-bar-top {
    position: absolute; left: 58px; top: 0;
    width: 16px; height: 150px;
    background: var(--blue);
  }
  .card-front .accent-bar-bottom {
    position: absolute; right: 0; bottom: 0;
    width: 16px; height: 230px;
    background: var(--blue);
  }
  .brand {
    display: flex; align-items: center; gap: 10px;
    color: var(--blue);
    font-weight: 700;
    letter-spacing: .5px;
    white-space: nowrap;
  }
  .brand-mark {
    background: var(--blue);
    flex: none;
  }
  .card-front .brand {
    position: absolute; left: 92px; top: 58px;
    font-size: 22px;
  }
  .card-front .brand-mark { width: 18px; height: 18px; }
  .divider {
    position: absolute; left: 278px; top: 150px;
    width: 1px; height: 130px;
    background: var(--blue);
  }
  .contact {
    position: absolute; left: 296px; top: 150px;
    color: var(--white);
    font-size: 13px;
    line-height: 1.45;
  }
  .contact .name {
    color: var(--blue);
    font-weight: 700;
    font-size: 18px;
    letter-spacing: .5px;
    line-height: 1.2;
  }
  .contact .role { margin-bottom: 6px; }
  .contact .line { display: flex; align-items: center; gap: 6px; }
  .contact .icon { width: 11px; height: 11px; flex: none; }
  .contact .address { margin-top: 6px; }

  /* Back: brand side */
  .card-back { display: flex; align-items: center; justify-content: center; }
  .card-back .brand { font-size: 38px; gap: 16px; }
  .card-back .brand-mark { width: 30px; height: 30px; }
</style>
</head>
<body>

  <section class="card card-front" aria-label="Business card, contact side">
    <div class="accent-bar-top"></div>
    <div class="brand"><span class="brand-mark"></span>RWT Fittings Ltd</div>
    <div class="divider"></div>
    <div class="contact">
      <div class="name">DALE ORWIN</div>
      <div class="role">Managing Director</div>
      <div class="line">
        <svg class="icon" viewBox="0 0 12 12" aria-hidden="true"><path fill="#29a9e1" d="M2.5 1 4.5 3.2 3.4 4.6a7 7 0 0 0 4 4L8.8 7.5 11 9.5 9.8 11C5 11 1 7 1 2.2Z"/></svg>
        <span>123 456 789</span>
      </div>
      <div class="line">
        <svg class="icon" viewBox="0 0 12 12" aria-hidden="true"><rect x="1" y="2.5" width="10" height="7" fill="#29a9e1"/><path d="M1 2.5 6 6.5 11 2.5" stroke="#1b1b1b" fill="none"/></svg>
        <span>info@rwtfittings-demo.com</span>
      </div>
      <div class="line">
        <svg class="icon" viewBox="0 0 12 12" aria-hidden="true"><circle cx="6" cy="6" r="5" fill="#29a9e1"/><path d="M1 6h10M6 1c-2.5 3-2.5 7 0 10M6 1c2.5 3 2.5 7 0 10" stroke="#1b1b1b" fill="none" stroke-width=".8"/></svg>
        <span>www.rwtfittings-demo.com</span>
      </div>
      <div class="address">Your address, City<br>State, Zip 1234</div>
    </div>
    <div class="accent-bar-bottom"></div>
  </section>

  <section class="card card-back" aria-label="Business card, brand side">
    <div class="brand"><span class="brand-mark"></span>RWT Fittings Ltd</div>
  </section>

</body>
</html>
```